specialised legal consultancy business needs an update on logo and office stationary.

Update on Logo - see attached.

update on email signature - something new and fresh with only the following details -

(the logo)
Advocate Pieter Vosloo
PV Entity Frameworks (Pty) Ltd (Reg No.: 2019 / 352917 / 07)
LLB, LLM (Cum Laude), Cert.Dir (BFNTA), FCG (PRWEK)
+27 61 552 9047
pieter#vosloolegal.com

Update on letterhead - something new and fresh and please more user-friendly. With the same details as per the email signature.

```html
<!DOCTYPE html>
<html lang="en">
<head>
<meta charset="utf-8">
<title>PV Entity Frameworks – Letterhead</title>
<link rel="stylesheet" href="https://fonts.googleapis.com/css2?family=Open+Sans:wght@400&family=Roboto:wght@400;500&display=swap">
<style>
  :root {
    --backdrop: #dcdcdc;
    --paper: #f8f8f8;
    --ink-strong: #111111;
    --ink-body: #666666;
    --ink-muted: #5a5a5a;
    --signature-ink: #1c2a44;
  }
  html, body {
    margin: 0;
    padding: 0;
    width: 1153px;
    height: 1200px;
    overflow: hidden;
    background: var(--backdrop);
  }
  .letterhead {
    position: absolute;
    left: 167px;
    top: 30px;
    width: 818px;
    height: 1140px;
    background: var(--paper);
    box-shadow: 0 10px 30px rgba(0,0,0,0.18);
    font-family: "Open Sans", sans-serif;
    color: var(--ink-body);
  }
  .brand {
    position: absolute;
    left: 71px;
    top: 120px;
    display: flex;
    align-items: center;
    gap: 10px;
  }
  .brand-square {
    width: 22px;
    height: 22px;
    background: var(--ink-strong);
  }
  .brand-name {
    font-family: "Roboto", sans-serif;
    font-weight: 500;
    font-size: 22px;
    letter-spacing: 2px;
    color: var(--ink-strong);
  }
  .company-details {
    position: absolute;
    left: 427px;
    top: 86px;
    font-family: "Roboto", sans-serif;
    font-size: 14.6px;
    line-height: 19px;
    color: var(--ink-muted);
  }
  .company-name {
    color: var(--ink-strong);
    font-weight: 500;
  }
  .contact-line {
    display: flex;
    align-items: center;
    gap: 4px;
  }
  .contact-line svg { flex: none; }
  .contact-gap { width: 6px; }
  .letter-body {
    position: absolute;
    left: 71px;
    top: 288px;
    width: 670px;
    font-size: 15px;
    line-height: 22px;
  }
  .letter-body p {
    margin: 0 0 22px;
    text-align: justify;
  }
  .letter-body .salutation,
  .letter-body .closing { text-align: left; }
  .signature {
    position: absolute;
    left: 71px;
    top: 869px;
    width: 97px;
    height: 90px;
    background: linear-gradient(135deg, rgba(28,42,68,0.12), rgba(28,42,68,0.04));
  }
  .credentials {
    position: absolute;
    left: 0;
    right: 0;
    top: 1056px;
    text-align: center;
    font-family: "Roboto", sans-serif;
    font-size: 12.5px;
    line-height: 21px;
    color: var(--ink-muted);
  }
  .credentials .sep {
    color: var(--ink-strong);
    font-weight: 500;
    margin: 0 4px;
  }
</style>
</head>
<body>
  <main class="letterhead">
    <div class="brand">
      <span class="brand-square"></span>
      <span class="brand-name">PV ENTITY</span>
    </div>

    <address class="company-details" style="font-style:normal">
      <div class="company-name">PV Entity Frameworks (Pty) Ltd</div>
      <div>Reg No.: 2019 / 352917 / 07</div>
      <div>47 Kameeldoring Avenue, Waterkloof Glen, Pretoria</div>
      <div class="contact-line">
        <svg width="14" height="11" viewBox="0 0 14 11" aria-hidden="true">
          <path d="M1 4 C1 1.5 13 1.5 13 4 L11 5 L10 3.5 H4 L3 5 Z" fill="#111"/>
          <rect x="3" y="5" width="8" height="5" rx="1" fill="#111"/>
        </svg>
        <span>+27 61 552 9047</span>
        <span class="contact-gap"></span>
        <svg width="14" height="11" viewBox="0 0 14 11" aria-hidden="true">
          <rect x="1" y="1" width="12" height="9" fill="none" stroke="#111" stroke-width="1.4"/>
          <path d="M1 1 L7 6 L13 1" fill="none" stroke="#111" stroke-width="1.4"/>
        </svg>
        <span>pieter#vosloolegal.com</span>
      </div>
    </address>

    <section class="letter-body">
      <p class="salutation">Dear customer,</p>
      <p>Lorem ipsum dolor sit amet, consectetur adipisicing elit, sed do eiusmod tempor incididunt ut labore et dolore magna aliqua. Ut enim ad minim veniam, quis nostrud exercitation ullamco laboris nisi ut aliquip ex ea commodo consequat. Duis aute irure dolor in reprehenderit in voluptate velit esse cillum dolore eu fugiat nulla pariatur. Excepteur sint occaecat cupidatat non proident, sunt in culpa qui officia deserunt mollit anim id est laborum.</p>
      <p>Lorem ipsum dolor sit amet, consectetur adipisicing elit, sed do eiusmod tempor incididunt ut labore et dolore magna aliqua. Ut enim ad minim veniam, quis nostrud exercitation ullamco laboris nisi ut aliquip ex ea commodo consequat. Duis aute irure dolor in reprehenderit in voluptate velit esse cillum dolore eu fugiat nulla pariatur. Excepteur sint occaecat cupidatat non proident, sunt in culpa qui officia deserunt mollit anim id est laborum.</p>
      <p>Lorem ipsum dolor sit amet, consectetur adipisicing elit, sed do eiusmod tempor incididunt ut labore et dolore magna aliqua. Ut enim ad minim veniam, quis nostrud exercitation ullamco laboris nisi ut aliquip ex ea commodo consequat. Duis aute irure dolor in reprehenderit in voluptate velit esse cillum dolore eu fugiat nulla pariatur. Excepteur sint occaecat cupidatat non proident, sunt in culpa qui officia deserunt mollit anim id est laborum.</p>
      <p>Lorem ipsum dolor sit amet, consectetur adipisicing elit, sed do eiusmod tempor incididunt ut labore et dolore magna aliqua. Ut enim ad minim veniam, quis nostrud exercitation ullamco laboris nisi ut aliquip ex ea commodo consequat. Duis aute irure dolor in reprehenderit.</p>
      <p class="closing">Yours Sincerely,</p>
    </section>

    <div class="signature" role="img" aria-label="Handwritten signature of Pieter Vosloo"></div>

    <footer class="credentials">
      <div>Advocate of the High Court<span class="sep">|</span>Mediator<span class="sep">|</span>Arbitrator<span class="sep">|</span>LLB, LLM (Cum Laude)<span class="sep">|</span>Cert.Dir (BFNTA), FCG (PRWEK)</div>
      <div>Chartered Secretary (PRWEK)<span class="sep">|</span>Member of Legal Advisers Guild of Southern Africa</div>
    </footer>
  </main>
</body>
</html>
```